Brovanek Data Yellow rose letterhead

I have a new logo for my company but in its current form it is too large to be used on letterhead or as a email signature. I need to have the designer use elements from the current logo and create something close to the original but more suited for smaller items.
Updates

I just uploaded a copy of our logo that does not have the weathered affect. Thanks

Reason: More time for revisions

Industry/Entity Type

It Company

Requirements
Must have
• The design must maintain the visual effect of the current logo. It needs to include the yellow rose and the name of the company.
Nice to have
• It would be nice to maintain the stamp theme and incorporate my name, address, phone, email. etc.

```html
<!DOCTYPE html>
<html lang="en">
<head>
<meta charset="utf-8">
<title>Brovanek Data Letterhead</title>
<link href="https://fonts.googleapis.com/css2?family=Arimo:wght@400;700&family=Michroma&display=swap" rel="stylesheet">
<style>
  :root {
    --backdrop: #b9b9b9;
    --paper: #ffffff;
    --earth: #5a4b44;
    --teal: #35b8bc;
    --gold: #f2c12e;
    --rose-light: #fde36a;
    --rose-deep: #f0b81c;
    --ink: #5a4b44;
  }
  * { margin: 0; padding: 0; box-sizing: border-box; }
  html, body {
    width: 848px; height: 1200px; overflow: hidden;
    background: var(--backdrop);
  }
  .letterhead {
    position: absolute; left: 105px; top: 152px;
    width: 637px; height: 898px;
    background: var(--paper);
    overflow: hidden;
  }
  .header-band {
    position: absolute; left: 0; top: 0; width: 100%; height: 77px;
    background: var(--earth);
  }
  .header-rule-gold {
    position: absolute; left: 0; top: 77px; width: 100%; height: 2px;
    background: var(--gold);
  }
  .header-rule-teal {
    position: absolute; left: 0; top: 79px; width: 100%; height: 3px;
    background: var(--teal);
  }
  .rose-emblem {
    position: absolute; left: 17px; top: 14px;
    width: 106px; height: 108px;
    border-radius: 48% 52% 46% 54% / 50% 46% 54% 50%;
    background: radial-gradient(circle at 48% 40%, var(--rose-light) 0%, var(--rose-deep) 75%);
    box-shadow: 5px 5px 0 var(--teal);
  }
  .brand-name {
    position: absolute; left: 170px; top: 21px; width: 300px;
    text-align: center;
    font-family: "Michroma", sans-serif;
    font-size: 23px; letter-spacing: 0.5px; line-height: 1;
    white-space: nowrap;
    color: var(--teal);
  }
  .brand-tagline {
    position: absolute; left: 170px; top: 52px; width: 300px;
    text-align: center;
    font-family: "Arimo", sans-serif;
    font-size: 16px; letter-spacing: 4px; line-height: 1;
    white-space: nowrap;
    color: #ffffff;
  }
  .sender {
    position: absolute; left: 17px; top: 832px;
    font-family: "Arimo", sans-serif; color: var(--ink);
  }
  .sender-name { font-size: 15px; font-weight: 700; }
  .sender-details { margin-top: 6px; font-size: 12px; white-space: nowrap; }
  .footer-band { position: absolute; left: 0; top: 870px; }
</style>
</head>
<body>
  <main class="letterhead">
    <div class="header-band"></div>
    <div class="header-rule-gold"></div>
    <div class="header-rule-teal"></div>
    <div class="rose-emblem" role="img" aria-label="Yellow rose illustration with teal shadow"></div>
    <div class="brand-name">Brovanek Data</div>
    <div class="brand-tagline">THE INSIGHT BUILDERS</div>

    <section class="sender">
      <p class="sender-name">Mara Velden, PhD</p>
      <p class="sender-details">418 NE Cedar Ridge Trail, Ste 2150, Marlow Springs, TX 76512,&nbsp; mara@brovanek-data.com,&nbsp; 1-800-555-0148</p>
    </section>

    <svg class="footer-band" width="637" height="28" viewBox="0 0 637 28" aria-hidden="true">
      <polygon points="0,5 414,5 433,28 0,28" fill="var(--earth)"/>
      <polyline points="0,4 415,4 434,27" fill="none" stroke="var(--gold)" stroke-width="2.5"/>
    </svg>
  </main>
</body>
</html>
```